Bright Harbor Painters Banner

Create a banner that displays and reinforces Bright Harbor Painters’ brand identity while promoting our interior painting services. The banner will be displayed at indoor venues through the winter. The design should be clean, professional, and visually recognizable to both new and returning customers. See attached design brief & logo source files.

```html
<!DOCTYPE html>
<html lang="en">
<head>
<meta charset="UTF-8">
<title>Bright Harbor Painters Banner</title>
<link rel="stylesheet" href="https://fonts.googleapis.com/css2?family=Montserrat:wght@300;400;700;800;900&display=swap">
<style>
  :root {
    --page-bg: #ebebeb;
    --charcoal: #3f4240;
    --charcoal-dark: #2f3231;
    --sage: #71955c;
    --white: #ffffff;
    --sticker-red: #d4161d;
    --workwear-navy: #262c3f;
    --shirt-white: #e9e6e2;
  }
  * { margin: 0; padding: 0; box-sizing: border-box; }
  html, body {
    width: 1200px; height: 636px; overflow: hidden;
    background: var(--page-bg);
    font-family: "Montserrat", Arial, sans-serif;
  }
  .banner {
    position: absolute; left: 99px; top: 118px;
    width: 1003px; height: 400px;
    overflow: hidden;
    background: var(--sage);
  }
  .interior-backdrop {
    position: absolute; left: 0; top: 0; width: 501px; height: 400px;
    background: linear-gradient(100deg, var(--charcoal-dark) 0%, #4a4d4b 55%, #5b5e5c 100%);
  }
  .service-list { position: absolute; left: 42px; top: 30px; list-style: none; }
  .service-list li {
    display: flex; align-items: center;
    height: 53px;
    color: var(--white); font-weight: 800; font-size: 32px; letter-spacing: 0.2px;
  }
  .service-list svg { width: 24px; height: 24px; margin-right: 9px; flex: none; }
  .painter-photo {
    position: absolute; left: 345px; top: 0; width: 290px; height: 314px;
    background: linear-gradient(180deg,
      rgba(233,230,226,0) 0%,
      rgba(233,230,226,0.55) 20%,
      var(--shirt-white) 45%,
      var(--workwear-navy) 62%,
      var(--workwear-navy) 100%);
    opacity: 0.9;
    border-radius: 46% 46% 0 0 / 22% 22% 0 0;
  }
  .sticker {
    position: absolute; left: 320px; top: 50px; width: 132px; height: 132px;
    border-radius: 50%; background: var(--sticker-red);
    box-shadow: 2px 4px 8px rgba(0,0,0,0.35);
  }
  .brand-name {
    position: absolute; left: 690px; top: 52px; width: 290px;
    color: var(--white); font-weight: 800; text-align: center;
    line-height: 1;
  }
  .brand-name .brand-top { display: block; font-size: 18px; letter-spacing: 1px; margin-bottom: 4px; }
  .brand-name .brand-main { display: block; font-size: 40px; letter-spacing: 0.5px; }
  .headline {
    position: absolute; left: 688px; top: 142px; width: 292px;
    color: var(--white); text-align: center;
  }
  .headline .primary { font-weight: 900; font-size: 44px; line-height: 44px; letter-spacing: 0.3px; }
  .headline .rule { height: 2px; background: var(--white); margin: 10px 2px 6px; }
  .headline .secondary { font-weight: 300; font-size: 44px; line-height: 46px; letter-spacing: 1px; }
  .cta-bar {
    position: absolute; left: 39px; top: 314px; width: 918px; height: 47px;
    display: flex; border-radius: 24px; overflow: hidden;
    box-shadow: 0 4px 8px rgba(0,0,0,0.25);
  }
  .cta-label {
    width: 462px; background: var(--white); color: var(--charcoal);
    display: flex; align-items: center; justify-content: center;
    font-weight: 800; font-size: 23.5px; letter-spacing: 0.6px;
  }
  .cta-label .accent { color: var(--sage); margin: 0 7px; }
  .cta-url {
    flex: 1; background: var(--charcoal); color: var(--white);
    display: flex; align-items: center; justify-content: center;
    font-weight: 800; font-size: 24px; letter-spacing: 1.2px;
  }
</style>
</head>
<body>
  <div class="banner">
    <div class="interior-backdrop" role="img" aria-label="Dimmed photo of a bright home interior with windows"></div>

    <ul class="service-list">
      <li><svg viewBox="0 0 24 24" aria-hidden="true"><circle cx="12" cy="12" r="12" fill="#71955c"/><path d="M6.5 12.5l3.5 3.5 7.5-7.5" fill="none" stroke="#3f4240" stroke-width="2.6" stroke-linecap="round" stroke-linejoin="round"/></svg>Walls</li>
      <li><svg viewBox="0 0 24 24" aria-hidden="true"><circle cx="12" cy="12" r="12" fill="#71955c"/><path d="M6.5 12.5l3.5 3.5 7.5-7.5" fill="none" stroke="#3f4240" stroke-width="2.6" stroke-linecap="round" stroke-linejoin="round"/></svg>Ceilings</li>
      <li><svg viewBox="0 0 24 24" aria-hidden="true"><circle cx="12" cy="12" r="12" fill="#71955c"/><path d="M6.5 12.5l3.5 3.5 7.5-7.5" fill="none" stroke="#3f4240" stroke-width="2.6" stroke-linecap="round" stroke-linejoin="round"/></svg>Trim</li>
      <li><svg viewBox="0 0 24 24" aria-hidden="true"><circle cx="12" cy="12" r="12" fill="#71955c"/><path d="M6.5 12.5l3.5 3.5 7.5-7.5" fill="none" stroke="#3f4240" stroke-width="2.6" stroke-linecap="round" stroke-linejoin="round"/></svg>Cabinets</li>
      <li><svg viewBox="0 0 24 24" aria-hidden="true"><circle cx="12" cy="12" r="12" fill="#71955c"/><path d="M6.5 12.5l3.5 3.5 7.5-7.5" fill="none" stroke="#3f4240" stroke-width="2.6" stroke-linecap="round" stroke-linejoin="round"/></svg>Drywall Repair</li>
    </ul>

    <div class="painter-photo" role="img" aria-label="Smiling painter in hard hat and overalls holding a paint roller"></div>

    <div class="sticker" role="img" aria-label="Red promotional sticker"></div>

    <div class="brand-name">
      <span class="brand-top">BRIGHT HARBOR</span>
      <span class="brand-main">PAINTERS</span>
    </div>

    <div class="headline">
      <div class="primary">INTERIOR<br>PAINTING</div>
      <div class="rule"></div>
      <div class="secondary">SERVICES</div>
    </div>

    <div class="cta-bar">
      <div class="cta-label">BOOK A<span class="accent">FREE ESTIMATE</span>AT</div>
      <div class="cta-url">WWW.BHPAINTERS.COM</div>
    </div>
  </div>
</body>
</html>
```